Brightmill Data Works

Our company is about IT hardwares and IT solutions. IT hardware such as PC, RAMS, storage and servers. IT solutions such as project management, BA. We are also selling new technology too.

Target Market(s)

Consumer, Small to Medium Business, Corporate

Requirements
Must have
• The business card must have the following:
• Name:
• Title:
• Contact Number:
• Email address:
• Website:
• Color: Must match the logo color upgrade

```html
<!DOCTYPE html>
<html lang="en">
<head>
<meta charset="utf-8">
<title>Brightmill Data Works – Business Card</title>
<link href="https://fonts.googleapis.com/css2?family=Lato:wght@400;700;900&display=swap" rel="stylesheet">
<style>
  :root {
    --stage: #1b1b1b;
    --card: #141414;
    --card-front-a: #1a1a1a;
    --card-front-b: #2b2b2b;
    --accent: #e8962a;
    --accent-deep: #d9821c;
    --ink-light: #f4f4f4;
    --ink-muted: #5f5f5f;
  }
  * { box-sizing: border-box; margin: 0; padding: 0; }
  html, body { width: 1200px; height: 900px; overflow: hidden; }
  body {
    background: var(--stage);
    font-family: "Lato", Arial, sans-serif;
    display: flex;
    flex-direction: column;
    align-items: center;
    justify-content: center;
    gap: 56px;
  }
  .card {
    position: relative;
    width: 600px;
    height: 343px;
    border-radius: 16px;
    overflow: hidden;
    box-shadow: 0 14px 36px rgba(0,0,0,.55);
  }
  /* Front */
  .card--front { display: flex; align-items: center; justify-content: center; }
  .card__texture {
    position: absolute; inset: 0;
    background: linear-gradient(135deg, var(--card-front-b) 0%, var(--card-front-a) 45%, var(--card-front-b) 75%, var(--card-front-a) 100%);
  }
  .brand {
    position: relative;
    display: flex; align-items: center; gap: 16px;
  }
  .brand__mark { width: 34px; height: 34px; background: var(--accent); }
  .brand__name {
    font-weight: 900;
    font-size: 38px;
    letter-spacing: 1px;
    text-transform: uppercase;
    color: var(--ink-light);
  }
  /* Back */
  .card--back { background: var(--card); }
  .card__edge {
    position: absolute; left: 0; right: 0; bottom: 0; height: 9px;
    background: var(--accent-deep);
  }
  .back__brand {
    position: absolute; left: 40px; top: 0; bottom: 9px; width: 250px;
    display: flex; align-items: center; justify-content: center; gap: 10px;
  }
  .back__brand .brand__mark { width: 20px; height: 20px; }
  .back__brand .brand__name { font-size: 21px; color: var(--ink-muted); letter-spacing: .5px; }
  .divider {
    position: absolute; left: 312px; top: 60px; height: 200px; width: 3px;
    background: var(--accent);
  }
  .contact {
    position: absolute; left: 340px; top: 72px; right: 24px;
    color: var(--ink-light);
  }
  .contact__name {
    font-size: 21px; color: var(--accent); text-transform: uppercase; font-weight: 400;
  }
  .contact__name strong { font-weight: 900; }
  .contact__title { font-size: 14px; margin-top: 2px; }
  .contact__list { list-style: none; margin-top: 28px; }
  .contact__item {
    display: flex; align-items: center; gap: 12px;
    font-size: 14.5px; margin-bottom: 10px;
  }
  .contact__icon { width: 16px; height: 14px; flex: none; }
  .contact__web {
    margin-top: 14px; font-size: 16px; font-weight: 900; color: var(--accent);
  }
</style>
</head>
<body>

  <section class="card card--front">
    <div class="card__texture" role="img" aria-label="Faint dark low-poly faceted background pattern"></div>
    <div class="brand">
      <span class="brand__mark"></span>
      <span class="brand__name">Brightmill Data Works</span>
    </div>
  </section>

  <section class="card card--back">
    <div class="back__brand">
      <span class="brand__mark"></span>
      <span class="brand__name">Brightmill Data Works</span>
    </div>
    <div class="divider"></div>
    <div class="contact">
      <h1 class="contact__name">Oliver <strong>Hensley</strong></h1>
      <p class="contact__title">Managing Director</p>
      <ul class="contact__list">
        <li class="contact__item">
          <svg class="contact__icon" viewBox="0 0 16 14" aria-hidden="true">
            <path d="M1 4 Q8 -1 15 4 L13 6 L11 4.5 L5 4.5 L3 6 Z" fill="#e8962a"/>
            <rect x="3" y="7" width="10" height="6" rx="1" fill="#e8962a"/>
          </svg>
          <span>01632 960418</span>
        </li>
        <li class="contact__item">
          <svg class="contact__icon" viewBox="0 0 16 14" aria-hidden="true">
            <rect x="1" y="2" width="14" height="10" fill="#e8962a"/>
            <path d="M1 2 L8 8 L15 2" fill="none" stroke="#141414" stroke-width="1.4"/>
          </svg>
          <span>admin@brightmilldata.co.uk</span>
        </li>
      </ul>
      <p class="contact__web">www.brightmilldata.co.uk</p>
    </div>
    <div class="card__edge"></div>
  </section>

</body>
</html>
```